Web design for small empirical brand consulting company that will sell a web-based brand tool

We need a totally new and very appealing website:
Purpose: We want to attract lots of potential customers with this website... especially, we want to sell our web-based tool valuquant®... we want to be perceived as innovative, trendy, but solid and reliable… we want customers go to the website, login at „valuquant®“ (see structure), and perceive how it works.. and the contacting us or in the near future being able to buy a login and work with the tool… so we want to a) inform (on the website or send the url to customers) and b) to „force“ potential customers getting in contact with us…
Structure (e.g.): Must Home, valuquant®, About us, Contact (incl. legal notice); we are open for more, Nice to have e.g. references/clients, press... for example, we publish a nice book in a couple of months and might want to show it somewhere on the website as well...)
Layout: We would like to have more/mainly figures - may be animated or something like that – in specific those on slides 7 and 8 as well as 6 and 9 (which would be for our web-based tool valuquant®...)... excellent, but simple and with few text…
Fonts: Eurostile; CMYK 100/23/100/19, CMYK 0/0/0/70
Logo: Would you please use the lorentavo-logo used in this file?
Social Media: we think that it might make sense to be connected to chatterbay, quipline and so on as well…
Phantasy: May be it is possible to have something between a classic marketing research and an e-commerce website... just a thought... because it is mainly about the new tool that will be assessable through a login... but customers might want to contact us or vice versa in order to check how the tool will work (btw: you do not have further info about valuquant® here... I know)… I dream of having a site where people go to and by components of our tool like at brimbo… click and buy and go for it…
It is possible to program it in php or java? Thanks.
Pages I personally like: Don’t know if that helps, but I personally like those websites just they seem so simple: http:// www.pellivarn.com/, http://www.craftelune.net/... but I am veeery open
Pages I do not like anymore: my own www.lorentavo.ch

```html
<!DOCTYPE html>
<html lang="de">
<head>
<meta charset="utf-8">
<title>lorentavo – References &amp; Contact</title>
<link rel="stylesheet" href="https://fonts.googleapis.com/css2?family=Exo:wght@400;500&family=Ubuntu:wght@400;500&display=swap">
<style>
  :root {
    --green-bright: #05a805;
    --green-neon: #07d407;
    --green-main: #1f6a1a;
    --green-panel: #1d7a1b;
    --grey-main: #4b4b4b;
    --grey-field: #3e3e3e;
    --black-main: #0e0f10;
    --line-light: rgba(255,255,255,0.45);
    --text-white: #ffffff;
    --text-muted: #3d3f41;
    --text-heading-dark: #4f5153;
    --page-bg: #ffffff;
    --head-font: "Exo", "Eurostile", sans-serif;
    --body-font: "Ubuntu", sans-serif;
  }
  html, body { margin: 0; padding: 0; overflow: hidden; }
  body { width: 1000px; height: 1200px; background: var(--page-bg); position: relative; font-family: var(--body-font); }
  .page { position: absolute; left: 161px; top: 26px; width: 709px; height: 1121px; overflow: hidden; }
  .page-bands { position: absolute; left: 0; top: 0; }
  .abs { position: absolute; }

  .section-rule { position: absolute; left: 0; width: 709px; height: 1px; background: var(--line-light); }
  .section-title { position: absolute; left: 0; width: 709px; text-align: center; font-family: var(--head-font); font-weight: 500; font-size: 20px; color: var(--text-white); letter-spacing: 0.5px; }
  .section-title span { background: var(--title-bg); padding: 0 24px; position: relative; }
  .title-gap { position: absolute; height: 3px; }

  .intro { position: absolute; left: 150px; width: 409px; text-align: center; font-size: 7.5px; line-height: 9px; color: #dfe9dc; }

  .ref-rule { position: absolute; left: 182px; width: 341px; height: 1px; background: rgba(255,255,255,0.12); }
  .tabs { position: absolute; left: 182px; display: flex; gap: 2px; }
  .tab { width: 52px; height: 21px; background: #fff; color: var(--green-bright); font-size: 6px; line-height: 21px; text-align: center; text-transform: uppercase; }
  .tab.is-active { background: var(--green-neon); color: #fff; }
  .tab-bar { position: absolute; left: 182px; width: 341px; height: 3px; background: var(--green-neon); }
  .ref-panel { position: absolute; left: 182px; width: 341px; height: 74px; background: var(--green-panel); }
  .ref-panel p { margin: 20px 0 0 26px; width: 300px; font-size: 7px; line-height: 10px; color: #e5eee3; }
  .client-badge { position: absolute; width: 62px; height: 54px; }
  .client-name { position: absolute; left: 0; width: 52px; text-align: center; font-family: var(--body-font); font-weight: 500; color: var(--green-bright); }

  .read-more { position: absolute; left: 460px; top: 541px; display: flex; align-items: center; gap: 5px; font-family: var(--head-font); font-size: 7px; color: #fff; text-transform: uppercase; }

  .form-label { position: absolute; left: 77px; top: 683px; font-family: var(--head-font); font-size: 11px; color: #fff; }
  .field { position: absolute; background: var(--grey-field); border-left: 7px solid var(--green-bright); font-size: 7.5px; color: #e6e6e6; box-sizing: border-box; padding-left: 10px; }
  .submit { position: absolute; left: 359px; top: 802px; width: 80px; height: 27px; background: var(--green-bright); border-left: 5px solid #1a5c16; box-sizing: border-box; color: #fff; font-family: var(--head-font); font-weight: 500; font-size: 11px; text-align: center; line-height: 27px; }
  .contact-icon { position: absolute; left: 496px; width: 28px; height: 28px; background: var(--green-bright); }
  .contact-text { position: absolute; left: 530px; font-family: var(--head-font); font-size: 9.5px; line-height: 11px; color: #fff; }

  .connect-title { position: absolute; left: 0; width: 709px; top: 890px; text-align: center; font-family: var(--head-font); font-size: 23px; color: var(--text-heading-dark); letter-spacing: 0.5px; }
  .social-row { position: absolute; left: 0; width: 709px; top: 929px; display: flex; justify-content: center; gap: 8px; }
  .social-chip { height: 26px; padding: 0 8px; background: var(--green-bright); color: #fff; font-size: 8px; line-height: 26px; }
  .footer-rule { position: absolute; left: 79px; width: 551px; height: 1px; background: #1b1c1e; }
  .footer-col-title { position: absolute; font-family: var(--head-font); font-size: 10px; color: var(--text-heading-dark); text-transform: uppercase; }
  .footer-col-text { position: absolute; width: 220px; font-size: 7.5px; line-height: 9.5px; color: var(--text-muted); }
  .copyright { position: absolute; left: 0; width: 709px; top: 1093px; text-align: center; font-size: 8.5px; color: var(--text-muted); }
</style>
</head>
<body>
<main class="page">
  <svg class="page-bands" width="709" height="1121" aria-hidden="true">
    <rect x="0" y="0" width="709" height="1121" fill="var(--black-main)"/>
    <polygon points="0,0 709,0 709,871 0,847" fill="var(--grey-main)"/>
    <polygon points="0,0 709,0 709,606 0,586" fill="var(--green-main)"/>
    <polygon points="0,0 709,0 709,8 0,37" fill="var(--green-bright)"/>
  </svg>

  <!-- References -->
  <section class="references">
    <div class="section-rule" style="top:72px"></div>
    <div class="title-gap" style="left:258px;top:71px;width:193px;background:var(--green-main)"></div>
    <div class="section-rule" style="top:72px;left:225px;width:42px;background:#fff;height:2px"></div>
    <div class="section-rule" style="top:72px;left:434px;width:42px;background:#fff;height:2px"></div>
    <h2 class="section-title" style="top:58px;margin:0">REFERENCES</h2>
    <p class="intro" style="top:85px;margin:0">Wir sind aufgrund unserer Erfahrung, unseres Wissens und unserer wissenschaftlich fundierten Herangehensweise die Spezialisten in der empirischen Markenberatung.</p>
    <p class="intro" style="top:112px;margin:0">Hier eine Auswahl unserer Arbeiten</p>

    <article class="reference">
      <div class="ref-rule" style="top:180px"></div>
      <svg class="client-badge" style="left:114px;top:217px" viewBox="0 0 62 54" aria-hidden="true">
        <circle cx="26" cy="27" r="26" fill="#fff"/><polygon points="50,21 60,27 50,33" fill="#fff"/>
      </svg>
      <div class="client-name" style="left:114px;top:235px;font-size:15px">velora</div>
      <div class="tabs" style="top:194px"><div class="tab is-active">Auftrag</div><div class="tab">Arbeit</div><div class="tab">Ergebnisse</div></div>
      <div class="tab-bar" style="top:215px"></div>
      <div class="ref-panel" style="top:218px"><p>Branding Research zur Erfassung der Markenwahrnehmung im Rahmen der Entwicklung und Umsetzung der strategischen Positionierung der VELORA</p></div>
    </article>

    <article class="reference">
      <div class="ref-rule" style="top:364px"></div>
      <svg class="client-badge" style="left:115px;top:403px" viewBox="0 0 62 54" aria-hidden="true">
        <circle cx="26" cy="27" r="26" fill="#fff"/><polygon points="50,21 60,27 50,33" fill="#fff"/>
      </svg>
      <div class="client-name" style="left:115px;top:423px;font-size:11px">kestrin</div>
      <div class="tabs" style="top:380px"><div class="tab is-active">Auftrag</div><div class="tab">Arbeit</div><div class="tab">Ergebnisse</div></div>
      <div class="tab-bar" style="top:401px"></div>
      <div class="ref-panel" style="top:404px"><p>Branding Research zur Erfassung der Markenwahrnehmung im Rahmen der Entwicklung und Umsetzung der strategischen Positionierung der VELORA</p></div>
    </article>

    <div class="read-more">
      <svg width="17" height="17" viewBox="0 0 17 17" aria-hidden="true"><circle cx="8.5" cy="8.5" r="7.5" fill="none" stroke="#fff" stroke-width="1.2"/><polyline points="7,5 10.5,8.5 7,12" fill="none" stroke="#fff" stroke-width="1.2"/></svg>
      <span>Read more</span>
    </div>
    <div class="ref-rule" style="top:564px"></div>
  </section>

  <!-- Contact -->
  <section class="contact">
    <div class="section-rule" style="top:641px"></div>
    <div class="title-gap" style="left:258px;top:640px;width:193px;background:var(--grey-main)"></div>
    <div class="section-rule" style="top:641px;left:225px;width:42px;background:#fff;height:2px"></div>
    <div class="section-rule" style="top:641px;left:434px;width:42px;background:#fff;height:2px"></div>
    <h2 class="section-title" style="top:628px;margin:0">CONTACT US</h2>

    <div class="form-label">MESSAGE US</div>
    <div class="field" style="left:77px;top:711px;width:171px;height:26px;line-height:26px">Full Name</div>
    <div class="field" style="left:268px;top:711px;width:171px;height:26px;line-height:26px;text-align:center">Email</div>
    <div class="field" style="left:77px;top:744px;width:362px;height:54px;padding-top:10px">Message</div>
    <div class="submit">SUBMIT</div>

    <div class="contact-icon" style="top:709px">
      <svg width="28" height="28" viewBox="0 0 28 28" aria-hidden="true"><polygon points="14,5 24,14 21,14 21,23 16,23 16,17 12,17 12,23 7,23 7,14 4,14" fill="#1a4d16"/></svg>
    </div>
    <div class="contact-text" style="top:712px">Lindenweg 14<br>CH - 8400 Marbach</div>
    <div class="contact-icon" style="top:741px">
      <svg width="28" height="28" viewBox="0 0 28 28" aria-hidden="true"><rect x="9" y="5" width="10" height="18" rx="2" fill="none" stroke="#1a4d16" stroke-width="2"/></svg>
    </div>
    <div class="contact-text" style="top:750px">+41 70 555 01 24</div>
    <div class="contact-icon" style="top:771px">
      <svg width="28" height="28" viewBox="0 0 28 28" aria-hidden="true"><path d="M5 12 Q14 5 23 12 L21 14 L18 12 L18 10 Q14 9 10 10 L10 12 L7 14 Z" fill="#1a4d16"/><rect x="8" y="15" width="12" height="8" rx="1" fill="#1a4d16"/></svg>
    </div>
    <div class="contact-text" style="top:778px">+41 40 555 02 68</div>
  </section>

  <!-- Footer -->
  <footer class="site-footer">
    <div class="connect-title">CONNECT WITH US</div>
    <div class="social-row">
      <span class="social-chip">chatterbay</span>
      <span class="social-chip">pictova</span>
      <span class="social-chip">quipline</span>
    </div>
    <div class="footer-rule" style="top:966px"></div>
    <div class="footer-col-title" style="left:104px;top:981px">Recent Post</div>
    <p class="footer-col-text" style="left:104px;top:1007px;margin:0">Lorem ipsum dolor sit amet, consectetur adipisicing elit, sed do eiusmod tempor incididunt ut labore et dolore magna aliqua. Ut enim ad minim veniam, quis nostrud exercitation ullamco laboris nisi ut aliquip ex ea commodo consequat.</p>
    <div class="footer-col-title" style="left:389px;top:981px">Latest News</div>
    <p class="footer-col-text" style="left:389px;top:1007px;margin:0">Lorem ipsum dolor sit amet, consectetur adipisicing elit, sed do eiusmod tempor incididunt ut labore et dolore magna aliqua. Ut enim ad minim veniam, quis nostrud exercitation ullamco laboris nisi ut aliquip ex ea commodo consequat.</p>
    <div class="footer-rule" style="top:1079px"></div>
    <div class="copyright">2014 &nbsp;|&nbsp; lorentavo &nbsp;|&nbsp; All Right Reserves</div>
  </footer>
</main>
</body>
</html>
```